Visitenkarten-Design
Zielgruppe
Zielgruppe sind Großhändler in der Elektrotechnik, Fachfirmen für Notbeleuchtung. Produkte: Notbeleuchtungssysteme, Not- und Sicherheitsleuchten, Akkumulatoren/Batterien (industrielle)
Aufgabenstellung
Optimale Darstellung des Logos und der Werte des Unternehmens. Einhaltung der Farben des Logos. Eher eine helle Businesskarte, nicht zu Dunkel.
Wir bitten, dass uns der Gewinner gleich für die ersten 6 Mitarbeiter, welche Visitenkarten in unserem Unternehmen benötigen, zu erstellen.
Die bestehende Visitenkarte kam leider nicht gut an. Falsche Farben und kein komplett abgestimmtes Design.
Die neue Visitenkarte soll gut zur Website passen und die Firma optimal repräsentieren.
!Bitte nicht die Farbe der bestehenden Visitenkarte benutzen sondern nur Farbtöne des Logos. Bitte nicht zwingend am bestehenden Design der Visitenkarte orientieren, wir möchten frische Ideen!

```html
<!DOCTYPE html>
<html lang="de">
<head>
<meta charset="utf-8">
<title>Lumaro Solutions – Visitenkarte</title>
<link rel="stylesheet" href="https://fonts.googleapis.com/css2?family=Montserrat:wght@400;500;700&display=swap">
<style>
  :root {
    --magenta: #b01a74;
    --magenta-deep: #8c1162;
    --purple: #7d2a7e;
    --ink: #3a3a3a;
    --paper: #ffffff;
    --backdrop: #e6e6e9;
  }
  * { box-sizing: border-box; margin: 0; padding: 0; }
  html, body { width: 1200px; height: 800px; overflow: hidden; }
  body {
    background: var(--backdrop);
    font-family: 'Montserrat', sans-serif;
    display: flex;
    align-items: center;
    justify-content: center;
    gap: 60px;
  }
  .card {
    width: 510px;
    height: 330px;
    position: relative;
    box-shadow: 0 12px 30px rgba(0,0,0,0.18);
  }
  /* Front */
  .card--front {
    background: linear-gradient(35deg, var(--magenta-deep) 0%, #95186a 45%, var(--purple) 100%);
    color: var(--paper);
    display: flex;
    flex-direction: column;
    align-items: center;
    justify-content: center;
  }
  .brand {
    display: flex;
    align-items: center;
    gap: 14px;
  }
  .brand__dot {
    width: 22px;
    height: 22px;
    border-radius: 50%;
    background: var(--paper);
  }
  .brand__name {
    font-size: 34px;
    font-weight: 500;
    line-height: 1.1;
  }
  .front__web {
    margin-top: 40px;
    font-size: 22px;
    font-weight: 400;
    letter-spacing: 0.5px;
  }
  /* Back */
  .card--back {
    background: var(--paper);
  }
  .company {
    position: absolute;
    top: 28px;
    right: 32px;
    text-align: right;
    color: var(--ink);
    font-size: 12px;
    font-style: normal;
    line-height: 1.4;
  }
  .company__name { font-weight: 700; }
  .person {
    position: absolute;
    top: 98px;
    left: 36px;
  }
  .person__name {
    color: var(--magenta);
    font-size: 27px;
    font-weight: 700;
    letter-spacing: 0.5px;
  }
  .person__role {
    color: var(--ink);
    font-size: 12.5px;
    line-height: 1.35;
    margin-top: 4px;
  }
  .contact {
    position: absolute;
    left: 36px;
    bottom: 30px;
    list-style: none;
  }
  .contact__item {
    display: flex;
    align-items: center;
    gap: 12px;
    margin-top: 6px;
    color: var(--magenta);
    font-size: 17px;
  }
  .contact__icon {
    width: 30px;
    height: 30px;
    background: var(--magenta);
    display: flex;
    align-items: center;
    justify-content: center;
  }
</style>
</head>
<body>
  <section class="card card--front">
    <div class="brand">
      <span class="brand__dot"></span>
      <span class="brand__name">Lumaro Solutions</span>
    </div>
    <p class="front__web">lumaro-solutions.com</p>
  </section>

  <section class="card card--back">
    <address class="company">
      <span class="company__name">Lumaro Solutions GmbH</span><br>
      Lindenweg 4<br>
      D-84032 Ahornfeld
    </address>

    <div class="person">
      <h1 class="person__name">MIRKO SELBERT</h1>
      <p class="person__role">Geschäftsführer<br>Managing Director</p>
    </div>

    <ul class="contact">
      <li class="contact__item">
        <span class="contact__icon">
          <svg width="18" height="18" viewBox="0 0 24 24" aria-hidden="true"><path fill="#fff" d="M6.6 10.8a15.1 15.1 0 0 0 6.6 6.6l2.2-2.2a1 1 0 0 1 1-.25 11.4 11.4 0 0 0 3.6.57 1 1 0 0 1 1 1V20a1 1 0 0 1-1 1A17 17 0 0 1 3 4a1 1 0 0 1 1-1h3.5a1 1 0 0 1 1 1c0 1.25.2 2.45.57 3.57a1 1 0 0 1-.25 1z"/></svg>
        </span>
        0170 5829134
      </li>
      <li class="contact__item">
        <span class="contact__icon">
          <svg width="18" height="18" viewBox="0 0 24 24" aria-hidden="true"><path fill="#fff" d="M6.6 10.8a15.1 15.1 0 0 0 6.6 6.6l2.2-2.2a1 1 0 0 1 1-.25 11.4 11.4 0 0 0 3.6.57 1 1 0 0 1 1 1V20a1 1 0 0 1-1 1A17 17 0 0 1 3 4a1 1 0 0 1 1-1h3.5a1 1 0 0 1 1 1c0 1.25.2 2.45.57 3.57a1 1 0 0 1-.25 1z"/></svg>
        </span>
        08531 36720 48
      </li>
      <li class="contact__item">
        <span class="contact__icon">
          <svg width="18" height="14" viewBox="0 0 20 14" aria-hidden="true"><rect x="1" y="1" width="18" height="12" fill="none" stroke="#fff" stroke-width="1.5"/><path d="M1 1l9 7 9-7" fill="none" stroke="#fff" stroke-width="1.5"/></svg>
        </span>
        mirko.selbert@lumaro-solutions.com
      </li>
    </ul>
  </section>
</body>
</html>
```